Business Card Design for Occupational Medicine Start Up Company

We need to design a professional business card. We are a healthcare company providing occupational medicine services to blue collar industries. We are professional, efficient and high quality service providers.

Target Market(s)

Blue Collar Industry: Shipbuilding, Ports, Trucking Companies; The Executives and Safety Officers for these companies

Industry/Entity Type

Healthcare

Contact Information for Business Card

Logo, Name, Title, Email, Phone

Other font styles liked:
• Please match our Brand Guide

Requirements
Must have
• Our Company Colors and Logo

```html
<!DOCTYPE html>
<html lang="en">
<head>
<meta charset="utf-8">
<title>CrewWell Clinics – Business Card</title>
<link href="https://fonts.googleapis.com/css2?family=Montserrat:wght@400;500;600;700&display=swap" rel="stylesheet">
<style>
  :root {
    --navy: #2a3282;
    --navy-deep: #222a70;
    --navy-light: #4a5bb5;
    --orange: #f5a83b;
    --sky: #29a8e0;
    --white: #ffffff;
    --stage: #e9eaee;
    --card-w: 620px;
    --card-h: 354px;
  }
  * { box-sizing: border-box; margin: 0; padding: 0; }
  html, body {
    width: 1200px; height: 874px; overflow: hidden;
    background: var(--stage);
    font-family: "Montserrat", sans-serif;
  }
  .stage {
    width: 1200px; height: 874px;
    display: flex; flex-direction: column;
    align-items: center; justify-content: center; gap: 60px;
  }
  .card {
    position: relative;
    width: var(--card-w); height: var(--card-h);
    border-radius: 18px; overflow: hidden;
    box-shadow: 0 6px 20px rgba(20, 24, 60, 0.18);
  }

  /* Back side */
  .card-back { background: var(--navy); }
  .back-texture {
    position: absolute; inset: 0;
    background:
      radial-gradient(ellipse 70% 90% at 85% 90%, rgba(120, 140, 220, 0.45), rgba(120, 140, 220, 0) 70%),
      radial-gradient(ellipse 60% 70% at 20% 15%, rgba(20, 24, 80, 0.55), rgba(20, 24, 80, 0) 70%),
      linear-gradient(125deg, var(--navy-deep) 0%, var(--navy) 50%, var(--navy-light) 100%);
  }
  .back-lockup {
    position: absolute; left: 300px; top: 150px;
    display: flex; align-items: center; gap: 16px;
    color: var(--white);
  }

  /* Brand lockup (shared) */
  .brand-dot {
    width: 44px; height: 44px; border-radius: 50%;
    background: var(--orange); flex: none;
  }
  .brand-name { font-weight: 600; line-height: 1; }
  .brand-name .word { display: block; font-size: 28px; letter-spacing: 1px; }
  .brand-name .sub { display: block; font-size: 11px; letter-spacing: 7px; margin-top: 6px; }

  /* Front side */
  .card-front { background: var(--white); }
  .front-wave { position: absolute; inset: 0; }
  .front-lockup {
    position: absolute; left: 60px; top: 72px;
    display: flex; align-items: center; gap: 16px;
    color: var(--navy);
  }
  .contact-block {
    position: absolute; right: 46px; top: 198px;
    text-align: right; color: var(--white);
  }
  .person-name {
    color: var(--orange); font-weight: 600;
    font-size: 22px; line-height: 27px; letter-spacing: 1px;
  }
  .person-title {
    font-size: 14px; line-height: 17px; font-weight: 500; margin-right: 6px;
  }
  .contact-list { list-style: none; margin-top: 10px; }
  .contact-list li {
    display: flex; justify-content: flex-end; align-items: center; gap: 10px;
    font-size: 13px; line-height: 20px;
  }
  .contact-list svg { width: 12px; height: 12px; flex: none; fill: var(--orange); }
</style>
</head>
<body>
<main class="stage">

  <section class="card card-back" aria-label="Business card back">
    <div class="back-texture" role="img" aria-label="Repeating brand pattern in deep blue tones"></div>
    <div class="back-lockup">
      <span class="brand-dot"></span>
      <span class="brand-name"><span class="word">CREWWELL</span><span class="sub">CLINICS</span></span>
    </div>
  </section>

  <section class="card card-front" aria-label="Business card front">
    <svg class="front-wave" viewBox="0 0 620 354" aria-hidden="true">
      <path d="M0,205 C25,262 95,292 215,300 L0,300 Z" fill="var(--orange)"/>
      <g transform="translate(0,-10)">
        <path d="M0,250 C100,310 220,318 310,280 C350,262 380,175 450,140 C520,105 585,100 620,112" fill="none" stroke="var(--white)" stroke-width="16"/>
        <path d="M0,250 C100,310 220,318 310,280 C350,262 380,175 450,140 C520,105 585,100 620,112" fill="none" stroke="var(--sky)" stroke-width="6"/>
      </g>
      <path d="M0,258 C100,318 220,326 310,288 C350,270 380,183 450,148 C520,113 585,108 620,120 L620,354 L0,354 Z" fill="var(--navy)"/>
    </svg>

    <div class="front-lockup">
      <span class="brand-dot"></span>
      <span class="brand-name"><span class="word">CREWWELL</span><span class="sub">CLINICS</span></span>
    </div>

    <div class="contact-block">
      <p class="person-name">MARK DELANEY</p>
      <p class="person-title">President</p>
      <ul class="contact-list">
        <li>555-014-2287
          <svg viewBox="0 0 24 24"><path d="M6.6 10.8a15 15 0 0 0 6.6 6.6l2.2-2.2a1 1 0 0 1 1-.25 11.4 11.4 0 0 0 3.6.57 1 1 0 0 1 1 1V20a1 1 0 0 1-1 1A17 17 0 0 1 3 4a1 1 0 0 1 1-1h3.5a1 1 0 0 1 1 1c0 1.25.2 2.45.57 3.57a1 1 0 0 1-.25 1z"/></svg>
        </li>
        <li>mark@crewwellclinics.com
          <svg viewBox="0 0 24 24"><path d="M2 5h20v14H2z M2 5l10 7 10-7"/></svg>
        </li>
        <li>www.crewwellclinics.com
          <svg viewBox="0 0 24 24"><circle cx="12" cy="12" r="10"/></svg>
        </li>
      </ul>
    </div>
  </section>

</main>
</body>
</html>
```